Ancient Art and Artifact information website

Hello Designers,
We are starting up a new website who talk abut and discusses an ancient arts artifacts. We would covering a wide range of countries ranging from Egypt, Greece, India, Syria, Rome, etc. My website name Bright Loom
Designs that fits with ancient theme and some kind of uniqueness would be accepted.
Requirements:
1) A home page design
2) Sub page design
3) A suitable logo
Sections can be added are featured ancient arts/places with short description followed by a more button, latest news, and comment section.
Add contents if you found relevant for this category of website. Ability to share the information through social media is desired.
Must be a responsive design. I look forward to designs which are mind blowing.
Number of Pages Required
2 page

```html
<!DOCTYPE html>
<html lang="en">
<head>
<meta charset="utf-8">
<title>Bright Loom – Ancient Arts &amp; Artifacts</title>
<link href="https://fonts.googleapis.com/css2?family=Raleway:wght@400;500;600;700&family=Roboto:wght@400;500;700&display=swap" rel="stylesheet">
<style>
:root{
  --peach:#f8d5b0;
  --orange:#c9560f;
  --orange-bright:#e0701e;
  --ink:#2a2118;
  --darker:#141312;
  --white:#ffffff;
  --muted:#5a4a3c;
}
*{margin:0;padding:0;box-sizing:border-box}
html,body{width:1200px;height:2765px;overflow:hidden}
body{position:relative;background:var(--peach);font-family:'Roboto',sans-serif;color:var(--ink)}
.abs{position:absolute}
.site-header{left:0;top:0;width:1200px;height:88px;background:var(--peach)}
.brand{left:250px;top:26px;width:160px;text-align:center;font-family:'Raleway',sans-serif;font-weight:700;font-size:19px;color:var(--orange);letter-spacing:.5px;line-height:36px;white-space:nowrap}
.nav a{position:absolute;top:41px;font-size:11px;font-weight:500;color:var(--ink);text-decoration:none;letter-spacing:.4px;white-space:nowrap}
.nav a.active{color:var(--orange)}
.hero{left:0;top:88px;width:1200px;height:447px;background:linear-gradient(180deg,#8fb4d6 0%,#c9a47a 35%,#a97650 70%,#6f5a3e 100%)}
.dots{left:572px;top:502px;display:flex;gap:5px}
.dots span{width:9px;height:9px;border-radius:50%;background:var(--orange-bright)}
.dots span.on{background:var(--orange)}
.welcome{left:0;top:535px;width:1200px;height:317px;background:var(--peach);text-align:center}
.eyebrow{font-family:'Raleway',sans-serif;font-weight:600;letter-spacing:6px;color:var(--ink);white-space:nowrap}
.big-title{font-family:'Raleway',sans-serif;font-weight:700;letter-spacing:8px;color:var(--orange);white-space:nowrap}
.welcome .eyebrow{position:absolute;left:0;width:1200px;top:32px;font-size:23px}
.welcome .big-title{position:absolute;left:0;width:1200px;top:52px;font-size:41px}
.welcome p{position:absolute;left:255px;width:690px;font-size:13px;line-height:18px;color:var(--ink);letter-spacing:.3px}
.artifacts{left:0;top:852px;width:1200px;height:505px;background:linear-gradient(160deg,#d2621a 0%,#c2520c 50%,#a8450a 100%)}
.artifacts h2{position:absolute;left:0;width:1200px;top:44px;text-align:center;font-family:'Raleway',sans-serif;font-weight:600;font-size:34px;letter-spacing:3px;color:var(--white);white-space:nowrap}
.art-item{position:absolute;color:var(--white);width:330px}
.art-item h3{font-family:'Raleway',sans-serif;font-weight:700;font-size:17px;letter-spacing:1px;white-space:nowrap}
.art-item p{font-size:10px;line-height:12px;margin-top:4px}
.art-item.right{text-align:right}
.art-item.right p{padding:0 0 0 170px}
.art-item.left p{padding:0 160px 0 0}
.art-thumb{position:absolute;width:104px;height:104px;border-radius:50%;border:4px solid var(--white)}
.center-mark{left:470px;top:1126px;width:200px;text-align:center;font-family:'Raleway',sans-serif;font-weight:700;font-size:22px;color:var(--white);letter-spacing:1px;white-space:nowrap}
.featured{left:0;top:1357px;width:1200px;height:547px;background:var(--peach)}
.featured .eyebrow{position:absolute;left:0;width:1200px;top:34px;text-align:center;font-size:27px;font-weight:500}
.featured .big-title{position:absolute;left:0;width:1200px;top:64px;text-align:center;font-size:36px}
.tile{position:absolute;width:230px;height:188px}
.news{left:0;top:1904px;width:1200px;height:516px;background:linear-gradient(180deg,#d4651d 0%,#c9560f 60%,#b84d0c 100%)}
.news .eyebrow{position:absolute;left:0;width:1200px;top:42px;text-align:center;font-size:25px;color:var(--white);font-weight:400}
.news .big-title{position:absolute;left:0;width:1200px;top:66px;text-align:center;font-size:44px;color:var(--white)}
.news .intro{position:absolute;left:290px;width:620px;top:132px;text-align:center;color:var(--white);font-size:12px;line-height:15px;letter-spacing:.4px}
.card{position:absolute;top:199px;width:232px;height:269px;background:var(--white)}
.card .pic{width:232px;height:140px}
.card h4{margin:16px 12px 0;font-family:'Raleway',sans-serif;font-weight:700;font-size:13px;color:var(--orange);letter-spacing:.6px;white-space:nowrap}
.card p{margin:8px 12px 0;font-size:9.5px;line-height:11.5px;color:var(--muted)}
.contact{left:0;top:2420px;width:1200px;height:308px;background:linear-gradient(180deg,#2b2927 0%,#1f1d1c 100%)}
.contact .eyebrow{position:absolute;left:0;width:1200px;top:38px;text-align:center;font-size:27px;color:var(--white);font-weight:400}
.contact .big-title{position:absolute;left:0;width:1200px;top:66px;text-align:center;font-size:41px;color:var(--orange-bright)}
.field{position:absolute;background:var(--white);font-size:8px;font-weight:700;letter-spacing:.8px;color:var(--ink);padding:8px 12px}
.submit{position:absolute;left:262px;top:261px;width:674px;height:36px;background:var(--darker);color:var(--white);text-align:center;line-height:36px;font-family:'Raleway',sans-serif;font-weight:700;font-size:12px;letter-spacing:3px}
.site-footer{left:0;top:2728px;width:1200px;height:37px;background:var(--darker)}
.site-footer p{position:absolute;left:270px;top:13px;font-size:9px;color:var(--orange-bright);letter-spacing:.4px}
</style>
</head>
<body>

<header class="abs site-header">
  <div class="abs brand">Bright Loom</div>
  <nav class="nav">
    <a class="active" style="left:452px" href="#">HOME</a>
    <a style="left:510px" href="#">ABOUT US</a>
    <a style="left:588px" href="#">BROWSE COUNTRY</a>
    <a style="left:720px" href="#">BLOGS</a>
    <a style="left:780px" href="#">NEWS</a>
    <a style="left:846px" href="#">FAQ</a>
    <a style="left:892px" href="#">CONTACT US</a>
  </nav>
</header>

<section class="abs hero" role="img" aria-label="Photo of Roman forum ruins with columns and arches under a blue sky"></section>
<div class="abs dots"><span class="on"></span><span></span><span></span><span></span><span></span></div>

<section class="abs welcome">
  <div class="eyebrow">WELCOME TO</div>
  <h1 class="big-title">BRIGHT LOOM</h1>
  <p style="top:112px">Welcome to Lorem ipsum dolor sit amet, consectetur adipiscing elit. Fusce fringilla iaculis ante vel ornareat orci non elit elementum efficitur. Donec nibh lectus, bibendum aclibero eu, sagittislips faucibus velean volutpat euismod odiovel mollis Donec tincidunt pretium urna in vulputatet facilisis, mi eget sodales tincidunt, neque quam blandit diamis eros vitae neque. Maecenas finibus mi magna, sit porer mauris tempud accam facilisis dignissim ipsum in congue.</p>
  <p style="top:235px">Donec tincidunt pretium urna in vulputate. Ut facilisis, mi eget sodales tincidunt, neque quam blandit diam, a aliquet felis eros vitae nes finibus mi magna, sit amet ullamcorper mauris tempus an posuere a neque sed accumsan. Nam facilisis dignissim ipsum in congue.</p>
</section>

<section class="abs artifacts">
  <h2>AN ANCIENT ARTS ARTIFACTS</h2>
</section>
<div class="abs center-mark">BRIGHT LOOM</div>

<div class="art-item right" style="left:116px;top:974px"><h3>EGYPT ANCIENT ARTS ARTIFACTS</h3><p>Vestiulum aclipsum diam sit amet quamveh icula elementum.</p></div>
<div class="art-thumb" role="img" aria-label="Photo of the Great Sphinx" style="left:457px;top:962px;background:linear-gradient(160deg,#5e8fc2,#c49a5e)"></div>

<div class="art-item left" style="left:734px;top:1002px"><h3>GREECE ANCIENT ARTS ARTIFACTS</h3><p>Vestiulum aclipsum diam sit amet quamveh icula elementum.</p></div>
<div class="art-thumb" role="img" aria-label="Photo of an ancient amphitheatre" style="left:623px;top:995px;background:linear-gradient(160deg,#6aa0d4,#b77a48)"></div>

<div class="art-item right" style="left:50px;top:1144px"><h3>SYRIA ANCIENT ARTS ARTIFACTS</h3><p>Vestiulum aclipsum diam sit amet quamveh icula elementum.</p></div>
<div class="art-thumb" role="img" aria-label="Photo of a domed mosque" style="left:387px;top:1115px;background:linear-gradient(160deg,#7fb0de,#a8744a)"></div>

<div class="art-item left" style="left:754px;top:1174px"><h3>INDIA &nbsp;ANCIENT ARTS ARTIFACTS</h3><p>Vestiulum aclipsum diam sit amet quamveh icula elementum.</p></div>
<div class="art-thumb" role="img" aria-label="Photo of a white marble mausoleum" style="left:639px;top:1151px;background:linear-gradient(160deg,#6b9fd2,#e8e2d6)"></div>

<div class="art-item right" style="left:164px;top:1266px"><h3>ROME ANCIENT ARTS ARTIFACTS</h3><p>Vestiulum aclipsum diam sit amet quamveh icula elementum.</p></div>
<div class="art-thumb" role="img" aria-label="Photo of a Roman temple facade" style="left:506px;top:1225px;background:linear-gradient(160deg,#8fb6da,#b88458)"></div>

<section class="abs featured">
  <div class="eyebrow">ARTS PLACES</div>
  <h2 class="big-title">FEATURED ANCIENT</h2>
  <div class="tile" role="img" aria-label="Photo of carved marble mausoleum arch" style="left:240px;top:132px;background:linear-gradient(160deg,#d9d6d0,#a9a39a)"></div>
  <div class="tile" role="img" aria-label="Photo of a stone pyramid under a blue sky" style="left:478px;top:132px;background:linear-gradient(180deg,#5d93cf 0%,#b8966a 45%,#8a6a45 100%)"></div>
  <div class="tile" role="img" aria-label="Photo of a carved stone sphinx statue" style="left:716px;top:132px;background:linear-gradient(180deg,#3f78c4 0%,#c8b49a 55%,#8e7a62 100%)"></div>
  <div class="tile" role="img" aria-label="Photo of an amphitheatre at sunset" style="left:240px;top:327px;background:linear-gradient(180deg,#f0a94a 0%,#b4683a 55%,#6b4630 100%)"></div>
  <div class="tile" role="img" aria-label="Photo of a baroque marble fountain" style="left:478px;top:327px;background:linear-gradient(180deg,#d8cdbc 0%,#a89a85 60%,#7e9a98 100%)"></div>
  <div class="tile" role="img" aria-label="Photo of old buildings and columns" style="left:716px;top:327px;background:linear-gradient(180deg,#c77a4e 0%,#b9875e 50%,#6d7a4a 100%)"></div>
</section>

<section class="abs news">
  <div class="eyebrow">ARTS PLACES</div>
  <h2 class="big-title">LATES NEWS</h2>
  <p class="intro">Donec tincidunt pretium urnavulputatet facilisis, megetsodales tinciduntneque quamblandit diama aliquetfelis eros vitae nequeaecenas finibus mmagna, sit amet ullamcorper mauris tempusenean posuere a neque sed accumsan. Nam facilisis dignissim ipsum in congue.</p>
  <article class="card" style="left:227px">
    <div class="pic" role="img" aria-label="Photo of Greek ruins and a tower" style="background:linear-gradient(180deg,#7aa9d6 0%,#b88a5c 60%,#7d6a48 100%)"></div>
    <h4>GREECE ANCIENT PLACES</h4>
    <p>Fusce mattis condimentum rutrulipsi blandit quamac libero finibus ullamcorper lipfermentum malipsuris. Nunc volutpat sem euismod necricies lorem eget est ornare, et dignissim elit ultrices. Aliquam sit ametuninia malesuada mauris idviamed.</p>
  </article>
  <article class="card" style="left:483px">
    <div class="pic" role="img" aria-label="Photo of an amphitheatre at sunset" style="background:linear-gradient(180deg,#f2b050 0%,#c06a34 55%,#6d4a32 100%)"></div>
    <h4>ROME ANCIENT PLACES</h4>
    <p>Fusce mattis condimentum rutrulipsi blandit quamac libero finibus ullamcorper lipfermentum malipsuris. Nunc volutpat sem euismod necricies lorem eget est ornare, et dignissim elit ultrices. Aliquam sit ametuninia malesuada mauris idviamed.</p>
  </article>
  <article class="card" style="left:739px">
    <div class="pic" role="img" aria-label="Photo of the sphinx and pyramid" style="background:linear-gradient(180deg,#5d8fcb 0%,#c9a471 55%,#9a7648 100%)"></div>
    <h4>EGYPT ANCIENT PLACES</h4>
    <p>Fusce mattis condimentum rutrulipsi blandit quamac libero finibus ullamcorper lipfermentum malipsuris. Nunc volutpat sem euismod necricies lorem eget est ornare, et dignissim elit ultrices. Aliquam sit ametuninia malesuada mauris idviamed.</p>
  </article>
</section>

<section class="abs contact">
  <div class="eyebrow">ARTS PLACES</div>
  <h2 class="big-title">CONTACT US</h2>
  <div class="field" style="left:262px;top:134px;width:333px;height:28px">NAME: *</div>
  <div class="field" style="left:603px;top:134px;width:333px;height:28px">EMAIL: *</div>
  <div class="field" style="left:262px;top:169px;width:674px;height:83px">MESSAGE</div>
  <div class="submit">SUBMIT YOUR MESSAGE</div>
</section>

<footer class="abs site-footer">
  <p>Copyright 2017 Bright Loom. All Rights Reserved.</p>
</footer>

</body>
</html>
```